Parcelwise HQ letterhead and envelope

Design a formal (8.5x11) letterhead and envelope for sales outreach and legal matters. Using design input from https://www.parcelwisehq.example/ and the attached documents.

Industry/Entity Type

Software Service

Requirements
Must have
• These 4 hex colors are our official colors:
• #355c98 [blue]
• #1eb1a2 [teal]
• #fdba12 [gold]
• #f1653b [orange]
• So no other colors besides these should be used.

```html
<!DOCTYPE html>
<html lang="en">
<head>
<meta charset="utf-8">
<title>Parcelwise HQ Letterhead</title>
<link href="https://fonts.googleapis.com/css2?family=Open+Sans:wght@300;400;700&display=swap" rel="stylesheet">
<style>
  :root {
    --blue: #355c98;
    --teal: #1eb1a2;
    --ink: #2f2f33;
    --paper: #ffffff;
    --backdrop: #e4e5e7;
    --sig: #d9dbe0;
  }
  * { box-sizing: border-box; margin: 0; padding: 0; }
  html, body { width: 1200px; height: 945px; overflow: hidden; }
  body {
    background: var(--backdrop);
    font-family: "Open Sans", Arial, sans-serif;
    position: relative;
  }
  .letterhead {
    position: absolute;
    left: 260px; top: 32px;
    width: 680px; height: 880px;
    background: var(--paper);
    overflow: hidden;
    box-shadow: 0 2px 8px rgba(0,0,0,0.08);
  }
  .top-band {
    position: absolute; left: 0; top: 0; width: 100%; height: 8px;
    background: var(--blue);
  }
  .brand {
    position: absolute; left: 58px; top: 62px;
    display: flex; align-items: center; gap: 10px;
  }
  .brand-dot {
    width: 26px; height: 26px; border-radius: 50%;
    background: var(--blue);
  }
  .brand-name {
    font-size: 27px; font-weight: 300; color: var(--blue); letter-spacing: 0.3px;
  }
  .contact {
    position: absolute; right: 48px; top: 34px;
    font-size: 9.5px; line-height: 13px; color: var(--ink);
    list-style: none;
  }
  .contact li { display: flex; align-items: center; gap: 5px; }
  .contact svg { width: 8px; height: 8px; flex: none; }
  .contact .plain { padding-left: 13px; }
  .letter {
    position: absolute; left: 72px; top: 245px; width: 520px;
    color: var(--ink);
  }
  .salutation {
    font-family: Arial, "Open Sans", sans-serif;
    font-weight: 700; font-size: 15px; margin-bottom: 14px;
  }
  .letter p {
    font-size: 13px; line-height: 17px; margin-bottom: 17px;
  }
  .signature {
    width: 150px; height: 54px; margin-top: 12px; margin-left: 4px;
    background: linear-gradient(90deg, var(--sig), #eef0f3);
    border-radius: 4px;
  }
  .footer-swoosh {
    position: absolute; left: 0; bottom: 0; width: 680px; height: 230px;
  }
  .footer-url {
    font-family: "Open Sans", Arial, sans-serif;
    font-size: 12px; letter-spacing: 1.6px; fill: var(--blue);
  }
</style>
</head>
<body>
  <main class="letterhead">
    <div class="top-band"></div>

    <header class="brand">
      <span class="brand-dot"></span>
      <span class="brand-name">Parcelwise HQ</span>
    </header>

    <ul class="contact">
      <li><svg viewBox="0 0 8 8"><rect width="8" height="8" rx="1.5" fill="#355c98"/></svg>(555) 010-4821</li>
      <li><svg viewBox="0 0 8 8"><rect x="1.5" y="0.5" width="5" height="7" rx="1" fill="none" stroke="#355c98"/></svg>(555) 010-7730</li>
      <li><svg viewBox="0 0 8 8"><rect y="1" width="8" height="6" rx="1" fill="#355c98"/></svg>jsmith@parcelwisehq.example</li>
      <li class="plain">42 Harbor Lane</li>
      <li class="plain">Eastfield, MI 49000</li>
    </ul>

    <section class="letter">
      <h2 class="salutation">Dear Mr. Harlan,</h2>
      <p>Lorem Ipsum is simply dummy text of the printing and typesetting industry. Lorem Ipsum has been the industry's standard dummy text ever since the 1500s, when an unknown printer took a galley of type and scrambled it to make a type specimen book. It has survived not only five centuries, but also the leap into electronic typesetting, remaining essentially unchanged.</p>
      <p>The standard chunk of Lorem Ipsum used since the 1500s is reproduced below for those interested. Sections 1.10.32 and 1.10.33 from "de Finibus Bonorum et Malorum" by Cornelius are also reproduced in their exact original form, accompanied by English versions from the 1914 translation by H. Rowan</p>
      <p>Lorem Ipsum is simply dummy text of the printing and typesetting industry. Lorem Ipsum has been the industry's standard dummy text ever since the 1500s, when an unknown printer took a galley of type and scrambled it to make a type specimen book. It has survived not only five centuries, but also the leap into electronic typesetting, remaining essentially unchanged. It was popularised in the</p>
      <div class="signature" role="img" aria-label="Handwritten signature of the sender"></div>
    </section>

    <svg class="footer-swoosh" viewBox="0 0 680 230">
      <defs>
        <path id="url-baseline" d="M0 190 Q380 185 680 35"/>
      </defs>
      <path d="M0 203 Q380 198 680 48" fill="none" stroke="#1eb1a2" stroke-width="7"/>
      <path d="M0 216 Q400 212 680 64 L680 230 L0 230 Z" fill="#355c98"/>
      <text class="footer-url" text-anchor="middle">
        <textPath href="#url-baseline" startOffset="70%">www.parcelwisehq.example</textPath>
      </text>
    </svg>
  </main>
</body>
</html>
```